business card

Business card for new business.
Red and black corporate colors.
Card can have an Indsutrial feel to it. Feel free to add Rust, Bolted steel, or graphics as you see fit. We provide highly specialized services to the below mentioned industries.
Keep information out of corners so that if I want I can choose rounded corners.
Information
- front. name - title - phone - email
- Rear
Refining - Rail - Infrastructure - Mining - Energy
Calgary - Edmonton - Fort McMurray - Revelstoke - Vancouver

```html
<!DOCTYPE html>
<html lang="en">
<head>
<meta charset="utf-8">
<title>Ironspan business card</title>
<link rel="stylesheet" href="https://fonts.googleapis.com/css2?family=PT+Sans:wght@400;700&family=Roboto+Condensed:wght@400;700&display=swap">
<style>
  :root {
    --backdrop: #3a3a3c;
    --card: #232324;
    --red: #e3121b;
    --white: #f2f2f2;
    --grey: #b9b9bb;
    --rule: #8a8a8c;
  }
  * { margin: 0; padding: 0; box-sizing: border-box; }
  html, body { width: 1200px; height: 900px; overflow: hidden; }
  body {
    background: var(--backdrop);
    display: flex;
    flex-direction: column;
    align-items: center;
    justify-content: center;
    gap: 40px;
    font-family: "PT Sans", Arial, sans-serif;
  }
  .card {
    width: 640px;
    height: 366px;
    background: var(--card);
    position: relative;
    box-shadow: 0 6px 18px rgba(0,0,0,0.45);
  }
  .card-rear {
    display: flex;
    flex-direction: column;
    align-items: center;
    padding-top: 78px;
  }
  .brand {
    display: flex;
    align-items: center;
    gap: 14px;
    margin-bottom: 30px;
  }
  .brand-mark { width: 18px; height: 18px; background: var(--red); }
  .brand-name {
    font-family: "PT Sans", Arial, sans-serif;
    font-weight: 700;
    font-size: 62px;
    letter-spacing: 1px;
    color: var(--grey);
    line-height: 1;
  }
  .service-list {
    color: var(--white);
    font-size: 16px;
    line-height: 1.3;
    text-align: center;
  }
  .dot { color: var(--red); padding: 0 3px; }
  .card-front {
    display: flex;
    align-items: center;
    justify-content: center;
    gap: 30px;
  }
  .identity { text-align: right; }
  .person-name {
    font-family: "Roboto Condensed", Arial, sans-serif;
    font-weight: 700;
    font-size: 36px;
    color: var(--red);
    line-height: 1;
  }
  .person-title {
    font-size: 17px;
    color: var(--white);
    margin-top: 3px;
  }
  .divider { width: 1px; height: 82px; background: var(--rule); }
  .contact-list { list-style: none; color: var(--white); font-size: 17px; }
  .contact-list li { display: flex; align-items: center; gap: 10px; line-height: 1.45; }
  .contact-list svg { width: 14px; height: 14px; fill: var(--red); flex: none; }
</style>
</head>
<body>
  <section class="card card-rear">
    <div class="brand">
      <span class="brand-mark"></span>
      <span class="brand-name">IRONSPAN</span>
    </div>
    <p class="service-list">
      Refining<span class="dot">•</span>Rail<span class="dot">•</span>Infrastructure<span class="dot">•</span>Mining<br>
      Energy<span class="dot">•</span>Calgary<span class="dot">•</span>Edmonton<span class="dot">•</span>Fort McMurray<br>
      Revelstoke<span class="dot">•</span>Vancouver
    </p>
  </section>

  <section class="card card-front">
    <div class="identity">
      <p class="person-name">MARCUS HALE</p>
      <p class="person-title">PRESIDENT</p>
    </div>
    <div class="divider"></div>
    <ul class="contact-list">
      <li>
        <svg viewBox="0 0 16 16" aria-hidden="true"><path d="M2 5c0-2 2-3 6-3s6 1 6 3v1h-3V5H5v1H2z M4 7h8l2 6H2z"/></svg>
        555 0142 8837
      </li>
      <li>
        <svg viewBox="0 0 16 16" aria-hidden="true"><path d="M1 3h14v10H1z" fill="none"/><path d="M1 3h14L8 9z M1 4.5l7 5.5 7-5.5V13H1z"/></svg>
        marcus@ironspan.com
      </li>
      <li>
        <svg viewBox="0 0 16 16" aria-hidden="true"><circle cx="8" cy="8" r="7"/><circle cx="6" cy="6" r="1.6" fill="#232324"/><circle cx="10.5" cy="10" r="1.3" fill="#232324"/></svg>
        www.ironspan.com
      </li>
    </ul>
  </section>
</body>
</html>
```